Young, dynamic furniture company needs a new business card design

We require a new business card design for our modern furniture company which supplies furniture and appliances to the property and development market.
Oakridge Interiors has become one of the leading furniture & appliance suppliers to the property market withing London. With over 10 years experience, we have increased our business to supply not only private landlords and managing agents, but also property developers, housing associations and local councils.
We offer not only a complete range of furniture which includes beds, wardrobes, dining sets and sofas, but also a high quality, full delivery and assembly service to help you with all our furnishing needs.

Target Market(s)

Private landlords, estate agents, letting agents, property management companies

Industry/Entity Type

Business

Contact Information for Business Card

Name,
Title,
Address,
Mobile,
Telephone,
Fax, Website, email address

Font styles to use
Sans Serif

Colors
3176b5
0555a3
85abd2
cfdeed

Requirements
Must have
• All the above information for each of our staff, along with our logo

```html
<!DOCTYPE html>
<html lang="en">
<head>
<meta charset="utf-8">
<title>Oakridge Interiors – Business Card</title>
<link rel="stylesheet" href="https://fonts.googleapis.com/css2?family=Open+Sans:wght@400;600;700&display=swap">
<style>
  :root {
    --bg: #e9edf2;
    --blue-light: #2aa3dc;
    --blue-mid: #1a8bcc;
    --blue-deep: #0a63ad;
    --navy: #2a4f9e;
    --ink: #1d1d1f;
    --paper: #ffffff;
    --paper-shade: #e4e6e8;
    --white: #ffffff;
    --pale: #cfdeed;
  }
  * { margin: 0; padding: 0; box-sizing: border-box; }
  html, body { width: 1200px; height: 780px; overflow: hidden; }
  body {
    background: var(--bg);
    font-family: "Open Sans", Arial, sans-serif;
    position: relative;
  }
  .card {
    position: absolute;
    width: 540px;
    height: 310px;
    border-radius: 4px;
    overflow: hidden;
    box-shadow: 0 10px 26px rgba(20, 40, 70, 0.22);
  }
  .card-front { left: 30px; top: 235px; background: var(--paper); }
  .card-back {
    left: 630px; top: 235px;
    background: radial-gradient(ellipse at 55% 45%, var(--blue-light) 0%, var(--blue-mid) 45%, var(--blue-deep) 100%);
  }
  .front-shape { position: absolute; inset: 0; }

  .brand {
    position: absolute;
    left: 34px;
    top: 118px;
    width: 230px;
  }
  .brand-row { display: flex; align-items: center; gap: 10px; }
  .brand-square { width: 22px; height: 22px; background: var(--navy); flex: none; }
  .brand-name {
    font-size: 22px; font-weight: 400; color: var(--ink);
    text-transform: uppercase; letter-spacing: 0.3px; line-height: 1;
  }
  .brand-tagline {
    margin: 7px 0 0 32px;
    font-size: 9.5px; color: #444; text-transform: uppercase; letter-spacing: 0.6px;
  }

  .contact {
    position: absolute;
    left: 298px; top: 40px;
    color: var(--white);
  }
  .person-name {
    font-size: 19px; font-weight: 700; color: var(--ink);
    text-transform: uppercase; line-height: 1;
  }
  .person-title { font-size: 12px; color: var(--ink); margin-top: 2px; }
  .address { font-size: 12px; line-height: 1.45; margin-top: 22px; }
  .lines { list-style: none; margin-top: 6px; }
  .lines li {
    display: flex; align-items: center; gap: 8px;
    font-size: 12px; line-height: 1; height: 20px;
  }
  .icon {
    width: 15px; height: 15px; background: var(--ink); flex: none;
    display: flex; align-items: center; justify-content: center;
  }
  .icon svg { width: 11px; height: 11px; }

  .back-brand {
    position: absolute; inset: 0;
    display: flex; flex-direction: column; align-items: center; justify-content: center;
    color: var(--white);
  }
  .back-brand .brand-square { background: var(--white); width: 30px; height: 30px; }
  .back-brand .brand-name { color: var(--white); font-size: 28px; }
  .back-brand .brand-tagline { color: var(--pale); margin: 10px 0 0 0; font-size: 11px; }
</style>
</head>
<body>

<section class="card card-front" aria-label="Business card front">
  <svg class="front-shape" viewBox="0 0 540 310" preserveAspectRatio="none" aria-hidden="true">
    <defs>
      <linearGradient id="frontBlue" x1="0" y1="0" x2="1" y2="1">
        <stop offset="0" stop-color="#1677c2"/>
        <stop offset="0.5" stop-color="#24a0da"/>
        <stop offset="1" stop-color="#0f6fb9"/>
      </linearGradient>
      <linearGradient id="paperShade" x1="0" y1="0" x2="1" y2="0">
        <stop offset="0" stop-color="#e6e8ea"/>
        <stop offset="1" stop-color="#ffffff"/>
      </linearGradient>
    </defs>
    <rect width="540" height="310" fill="url(#paperShade)"/>
    <path d="M262 0 C 300 90, 232 200, 282 310 L540 310 L540 0 Z" fill="#1d1d1f"/>
    <path d="M272 0 C 312 90, 244 200, 292 310 L540 310 L540 0 Z" fill="url(#frontBlue)"/>
  </svg>

  <div class="brand">
    <div class="brand-row">
      <span class="brand-square"></span>
      <span class="brand-name">Oakridge Interiors</span>
    </div>
    <p class="brand-tagline">Trade Furniture Solutions</p>
  </div>

  <div class="contact">
    <h1 class="person-name">Daniel Reeve</h1>
    <p class="person-title">Manager</p>
    <p class="address">14 Elm Row, Suite 2<br>Camden, London NW1 4QT, UK</p>
    <ul class="lines">
      <li><span class="icon"><svg viewBox="0 0 12 12"><path d="M3 1h2l1 3-1.5 1a6 6 0 0 0 2.5 2.5L8 6l3 1v2a1 1 0 0 1-1 1A9 9 0 0 1 2 2a1 1 0 0 1 1-1z" fill="#fff"/></svg></span>07700 900 418</li>
      <li><span class="icon"><svg viewBox="0 0 12 12"><rect x="2" y="3" width="8" height="7" fill="#fff"/><rect x="4" y="1" width="4" height="3" fill="#fff"/></svg></span>020 7946 0321</li>
      <li><span class="icon"><svg viewBox="0 0 12 12"><rect x="1" y="4" width="10" height="6" fill="#fff"/><rect x="3" y="1" width="6" height="4" fill="none" stroke="#fff"/></svg></span>020 7946 0322</li>
      <li><span class="icon"><svg viewBox="0 0 12 12"><rect x="1" y="3" width="10" height="7" fill="#fff"/><path d="M1 3l5 4 5-4" fill="none" stroke="#1d1d1f"/></svg></span>daniel@oakridgeinteriors.co.uk</li>
      <li><span class="icon"><svg viewBox="0 0 12 12"><circle cx="6" cy="6" r="4.5" fill="none" stroke="#fff"/><path d="M1.5 6h9M6 1.5c-2.5 3-2.5 6 0 9M6 1.5c2.5 3 2.5 6 0 9" fill="none" stroke="#fff" stroke-width="0.8"/></svg></span>www.oakridgeinteriors.co.uk</li>
    </ul>
  </div>
</section>

<section class="card card-back" aria-label="Business card back">
  <div class="back-brand">
    <div class="brand-row">
      <span class="brand-square"></span>
      <span class="brand-name">Oakridge Interiors</span>
    </div>
    <p class="brand-tagline">Trade Furniture Solutions</p>
  </div>
</section>

</body>
</html>
```